Dog Snacks brand needs a new packaging design

Dear Designers,

We are looking for a packaging expert to design our new line of Dog Snacks which contain a relaxing hemp extract (CBD).

Our company is already selling various relaxing cat & dog products , and we would like this new design to reflect the same "style & feeling" as our current products (see attached instructions).

Technical aspects:
- The packaging is a Stand Up Pouch (12x18.5x7cm - see attached instructions).
- Please follow technical guidelines from printer (see attached instructions).
- The packaging will contain 120g of high-quality, semi-moist dog snacks.
- We will be designing 3 differents variations for 3 different flavours: Chicken, Beef & Liver.
- The packaging will be printed with a matt finish.

Design aspects:
- The design should be compatible with our brand identity (i.e. fluffly, pure, relaxing, positive, clean & natural).
- Soft/rounded shapes are preferred.
- Please use our brand's colors (#3BA384, White & Black).
- Please use our company logo (see attached instructions).
- The design also needs to convey a strong sense of professionalism as we are an animal "healthcare" brand.
- If you want to include a dog picture, we would prefer you to use a picture of our official brand ambassador (see attached instructions).
- We have attached a number of packaging examples which we like a lot. (see attached instructions). Please only use those as general inspiration.
- Only original work (no plagiarism will be accepted).

Please don't hesitate to send us a message if you have any questions about the brand, the product or the design requirements.

We look forward to seeing your designs & working on this together !

Thanks & regards,
Tobias

Target Market(s)

Dog owners

Industry/Entity Type

Pet Care

Font styles to use
Sans Serif

Requirements
Must have
• Please see project description.
Nice to have
Should not have

```html
<!DOCTYPE html>
<html lang="en">
<head>
<meta charset="utf-8">
<title>VerdaBites Relaxing Treats – Chicken Recipe</title>
<link rel="stylesheet" href="https://fonts.googleapis.com/css2?family=Montserrat:wght@500;600;700&family=Roboto+Condensed:wght@300;700&display=swap">
<style>
  :root{
    --brand-green:#389c80;
    --band-green:#6fae9b;
    --ink:#0b0b0b;
    --white:#ffffff;
    --recipe-orange:#d4952c;
    --treat-tan:#b59868;
    --photo-light:#ecebea;
    --photo-mid:#d9cfca;
  }
  *{margin:0;padding:0;box-sizing:border-box}
  html,body{width:739px;height:1200px;overflow:hidden;background:var(--white)}
  .pouch{position:relative;width:739px;height:1200px;overflow:hidden;background:var(--white);font-family:"Montserrat",sans-serif}
  .pouch__art{position:absolute;inset:0;z-index:0}
  .layer{position:absolute;z-index:2}
  .brand-name{left:251px;width:237px;top:242px;text-align:center;color:var(--white);font-weight:600;font-size:36px;letter-spacing:1px}
  .title{left:52px;color:var(--brand-green);font-weight:600;font-size:88px;letter-spacing:-2px;line-height:1;top:460px}
  .subtitle{left:57px;top:543px;color:var(--ink);font-weight:700;font-size:70px;letter-spacing:12px;line-height:1}
  .rule{height:4px;background:var(--brand-green)}
  .rule--top{left:62px;top:634px;width:274px}
  .rule--bottom{left:62px;top:715px;width:235px}
  .dose{left:60px;top:658px;font-weight:700;font-size:38px;letter-spacing:-1px;line-height:1}
  .dose__key{color:var(--brand-green)}
  .dose__value{color:var(--ink)}
  .audience{left:64px;top:758px;font-family:"Roboto Condensed",sans-serif;font-weight:300;font-size:29px;line-height:31px;color:var(--brand-green);white-space:nowrap}
  .recipe{left:50px;top:900px;width:166px;text-align:center;color:var(--white);font-family:"Roboto Condensed",sans-serif;line-height:1}
  .recipe__flavour{display:block;font-weight:700;font-size:31px;letter-spacing:-0.5px}
  .recipe__word{display:block;font-weight:300;font-size:27px;margin-top:1px}
  .product-name{left:192px;top:1008px;font-family:"Roboto Condensed",sans-serif;font-weight:300;font-size:88px;letter-spacing:-2px;color:var(--brand-green);line-height:1;white-space:nowrap}
  .product-name sup{font-size:20px;vertical-align:top;position:relative;top:10px;margin-left:4px}
  .benefits{left:0;right:0;top:1095px;height:105px;background:var(--band-green);z-index:3}
  .benefits__text{position:absolute;left:0;right:0;top:31px;text-align:center;color:var(--white);font-weight:600;font-size:20px;letter-spacing:6px}
  .claim-text{font-family:"Montserrat",sans-serif;font-weight:600;font-size:10.5px;letter-spacing:1px;fill:var(--brand-green)}
</style>
</head>
<body>
<main class="pouch">
  <svg class="pouch__art" width="739" height="1200" viewBox="0 0 739 1200" xmlns="http://www.w3.org/2000/svg">
    <defs>
      <linearGradient id="photoTone" x1="0" y1="0" x2="1" y2="1">
        <stop offset="0" stop-color="var(--photo-light)"/>
        <stop offset="0.55" stop-color="var(--photo-mid)"/>
        <stop offset="1" stop-color="var(--photo-light)"/>
      </linearGradient>
      <path id="ringTop" d="M556,156 a44,44 0 1 1 88,0"/>
      <path id="ringBottom" d="M548,156 a52,52 0 1 0 104,0"/>
      <path id="ringTop2" d="M556,282 a44,44 0 1 1 88,0"/>
      <path id="ringBottom2" d="M548,282 a52,52 0 1 0 104,0"/>
      <path id="ringTop3" d="M556,404 a44,44 0 1 1 88,0"/>
      <path id="ringBottom3" d="M548,404 a52,52 0 1 0 104,0"/>
    </defs>

    <rect class="header-band" x="0" y="62" width="739" height="22" fill="var(--brand-green)"/>
    <path class="brand-tab" d="M251,0 H488 V288 a62,62 0 0 1 -62,62 H313 a62,62 0 0 1 -62,-62 Z" fill="var(--brand-green)"/>
    <path class="brand-tab__fold" d="M251,62 H488 V84 C420,84 378,110 370,156 C362,110 320,84 251,84 Z" fill="var(--white)"/>

    <g class="claim-badge">
      <text class="claim-text"><textPath href="#ringTop" startOffset="50%" text-anchor="middle">ANIMAL WELL-BEING</textPath></text>
      <text class="claim-text"><textPath href="#ringBottom" startOffset="50%" text-anchor="middle">ANIMAL WELL-BEING</textPath></text>
      <circle cx="600" cy="158" r="22" fill="var(--brand-green)" role="img" aria-label="Paw print with a cross icon"/>
    </g>
    <g class="claim-badge">
      <text class="claim-text"><textPath href="#ringTop2" startOffset="50%" text-anchor="middle">REDUCES STRESS</textPath></text>
      <text class="claim-text"><textPath href="#ringBottom2" startOffset="50%" text-anchor="middle">REDUCES STRESS</textPath></text>
      <circle cx="600" cy="284" r="22" fill="none" stroke="var(--brand-green)" stroke-width="2" role="img" aria-label="Calm sleeping dog face icon"/>
    </g>
    <g class="claim-badge">
      <text class="claim-text"><textPath href="#ringTop3" startOffset="50%" text-anchor="middle">HEMP EXTRACT</textPath></text>
      <text class="claim-text"><textPath href="#ringBottom3" startOffset="50%" text-anchor="middle">HEMP EXTRACT</textPath></text>
      <circle cx="600" cy="406" r="22" fill="var(--brand-green)" role="img" aria-label="Hemp leaf icon"/>
    </g>

    <path class="hero-swoosh" d="M739,622 C560,590 330,690 292,850 C276,925 292,990 318,1030 L360,1030 C336,990 322,935 322,885 C330,745 540,660 739,652 Z" fill="var(--brand-green)"/>
    <path class="hero-photo" d="M739,652 C540,660 330,745 322,885 C322,960 345,1040 380,1095 H739 Z" fill="url(#photoTone)" role="img" aria-label="Photo of a white wrinkled dog looking up calmly at a blue butterfly on its nose"/>

    <rect class="audience-icon" x="180" y="752" width="64" height="62" rx="20" fill="var(--brand-green)" role="img" aria-label="Silhouettes of a large and a small dog"/>

    <ellipse class="recipe-badge" cx="133" cy="939" rx="84" ry="80" fill="var(--recipe-orange)"/>
    <ellipse cx="133" cy="939" rx="74" ry="70" fill="none" stroke="var(--white)" stroke-width="2.5" stroke-dasharray="7 5"/>
    <rect class="treats-photo" x="192" y="878" width="130" height="114" rx="36" fill="var(--treat-tan)" role="img" aria-label="Photo of two bone-shaped chicken dog treats"/>
  </svg>

  <div class="layer brand-name">VERDALO</div>

  <h1 class="layer title">RELAXING</h1>
  <div class="layer subtitle">TREATS</div>

  <div class="layer rule rule--top"></div>
  <div class="layer dose"><span class="dose__key">CBD</span> <span class="dose__value">250MG</span></div>
  <div class="layer rule rule--bottom"></div>

  <p class="layer audience">For dogs<br>of all sizes</p>

  <div class="layer recipe">
    <span class="recipe__flavour">CHICKEN</span>
    <span class="recipe__word">RECIPE</span>
  </div>

  <div class="layer product-name">VerdaBites<sup>TM</sup></div>

  <footer class="layer benefits">
    <p class="benefits__text">CALMS | SOOTHES | RELAXES</p>
  </footer>
</main>
</body>
</html>
```